Boutique custom software development company needs new business card

Our nearly 20 year old custom software development company would like to better include the fact that we are now providing Bitcoin services. These new services are B2B include education (how to acquire and securely hold Bitcoin) and integrating Bitcoin payments into existing ecommerce sites or other existing systems. Please keep the card clean and simple. Attached is our current design and some other files. vextorial.com

Target Market(s)

businesses owners interested in long term relationship

Industry/Entity Type

Custom software development and Bitcoin

Contact Information for Business Card

Dale Parker, dale@vextorial.com, vextorial.com, (888) 555-VXTRL

Font styles to use
Other font styles liked:
• monospace

Requirements
Must have
• double-sided
Nice to have
• clean and simple
Should not have
• physical address

```html
<!DOCTYPE html>
<html lang="en">
<head>
<meta charset="utf-8">
<title>Vextorial – Business Card</title>
<link rel="stylesheet" href="https://fonts.googleapis.com/css2?family=Open+Sans:wght@400;700;800&display=swap">
<style>
  :root {
    --blue: #3b73b9;
    --blue-deep: #1f5197;
    --blue-soft: #6f93cc;
    --orange: #ef7d22;
    --white: #ffffff;
    --backdrop: #ababab;
    --font: "Open Sans", Arial, sans-serif;
  }
  * { box-sizing: border-box; margin: 0; padding: 0; }
  html, body { width: 1200px; height: 936px; overflow: hidden; }
  body {
    background: var(--backdrop);
    font-family: var(--font);
    display: flex;
    flex-direction: column;
    align-items: center;
    justify-content: center;
    gap: 44px;
  }
  .card {
    position: relative;
    width: 700px;
    height: 400px;
    overflow: hidden;
    box-shadow: 0 6px 18px rgba(0,0,0,.25);
  }

  /* Front */
  .card-front { background: var(--white); }
  .front-shapes { position: absolute; inset: 0; }
  .holder-name {
    position: absolute;
    left: 0; top: 36px;
    display: flex; align-items: center;
    font-weight: 800;
    font-size: 30px;
    line-height: 1;
    letter-spacing: .5px;
  }
  .name-tab {
    width: 30px; height: 30px;
    background: var(--orange);
    margin-right: 8px;
  }
  .name-first { color: var(--orange); margin-right: 10px; }
  .name-last { color: var(--blue); }

  .brand {
    position: absolute;
    right: 34px; top: 92px;
    text-align: right;
    color: var(--blue);
  }
  .brand-row { display: flex; align-items: center; justify-content: flex-end; gap: 10px; }
  .brand-mark { width: 30px; height: 30px; background: var(--orange); flex: none; }
  .brand-name {
    font-weight: 800;
    font-size: 50px;
    line-height: 1;
    letter-spacing: 1px;
  }
  .brand-tagline { font-size: 18px; margin-top: 6px; }

  .contact {
    position: absolute;
    right: 36px; bottom: 30px;
    list-style: none;
    color: var(--white);
    font-size: 18px;
    line-height: 1.5;
    text-align: right;
  }
  .contact li { display: flex; align-items: center; justify-content: flex-end; gap: 10px; }
  .contact-icon { width: 20px; height: 20px; flex: none; }

  /* Back */
  .card-back { background: var(--blue); }
  .back-texture { position: absolute; inset: 0; }
  .back-brand {
    position: absolute;
    left: 50%; top: 50%;
    transform: translate(-50%, -50%);
    color: var(--white);
    text-align: left;
    white-space: nowrap;
  }
  .back-brand .brand-row { justify-content: flex-start; }
  .back-brand .brand-tagline { margin-left: 40px; }
</style>
</head>
<body>

  <section class="card card-front" aria-label="Business card, front">
    <svg class="front-shapes" width="700" height="400" viewBox="0 0 700 400" aria-hidden="true">
      <polygon points="0,150 170,78 232,200 700,200 700,400 0,400" fill="var(--blue)"/>
      <line x1="212" y1="120" x2="292" y2="400" stroke="var(--white)" stroke-width="9"/>
      <rect x="0" y="196" width="22" height="44" fill="var(--orange)"/>
    </svg>

    <div class="holder-name">
      <span class="name-tab"></span>
      <span class="name-first">Dale</span>
      <span class="name-last">Parker</span>
    </div>

    <div class="brand">
      <div class="brand-row">
        <span class="brand-mark"></span>
        <span class="brand-name">VEXTORIAL</span>
      </div>
      <div class="brand-tagline">custom applications &amp; bitcoin services</div>
    </div>

    <ul class="contact">
      <li>(888) 555-VXTRL
        <svg class="contact-icon" viewBox="0 0 20 20" aria-hidden="true"><path d="M5 2l3 4-2 2c1 2.5 3 4.5 6 6l2-2 4 3-2 3C9 18 2 11 2 4z" fill="var(--orange)"/></svg>
      </li>
      <li>vextorial.com
        <svg class="contact-icon" viewBox="0 0 20 20" aria-hidden="true"><circle cx="10" cy="10" r="8" fill="none" stroke="var(--orange)" stroke-width="2"/><path d="M2 10h16M10 2c-3 3-3 13 0 16M10 2c3 3 3 13 0 16" fill="none" stroke="var(--orange)" stroke-width="1.5"/></svg>
      </li>
      <li>dale@vextorial.com
        <svg class="contact-icon" viewBox="0 0 20 20" aria-hidden="true"><rect x="2" y="5" width="16" height="11" fill="var(--orange)"/><path d="M2 5l8 6 8-6" fill="none" stroke="var(--white)" stroke-width="1.4"/></svg>
      </li>
    </ul>
  </section>

  <section class="card card-back" aria-label="Business card, back">
    <svg class="back-texture" width="700" height="400" viewBox="0 0 700 400" role="img" aria-label="Repeating brand symbol pattern across the card">
      <defs>
        <linearGradient id="backGlow" x1="0" y1="1" x2="1" y2="0">
          <stop offset="0" stop-color="var(--blue-deep)"/>
          <stop offset=".6" stop-color="var(--blue)"/>
          <stop offset="1" stop-color="var(--blue-soft)"/>
        </linearGradient>
      </defs>
      <rect width="700" height="400" fill="url(#backGlow)"/>
    </svg>

    <div class="back-brand">
      <div class="brand-row">
        <span class="brand-mark"></span>
        <span class="brand-name">VEXTORIAL</span>
      </div>
      <div class="brand-tagline">custom applications &amp; bitcoin services</div>
    </div>
  </section>

</body>
</html>
```